Fitness Nutrition Book to be designed

My business is an Online Fitness Training Business.
I have created a nutritional booklet that each online client will receive.
The booklet in total is 17 pages, which includes front and back cover.
Text has all been completed.
The booklet should be easy to read and using colors that convey energy, such as blues, blacks, greys, yellows, reds, etc.
I do not have photos of clients working out, but I would like to use photos that represent fitness.
Appropriate items would be Kettle Bells, Dumbbells, Battle Ropes and Slam balls
I would like the interior pages to have motivational quotes, creatively and eye catching, placed on the pages.
Quotes such as:
"If it doesn't challenge you, It wont change you!"
"Train insane or remain the same"
"Sweat is Fat Crying"
"Sore Today Strong Tomorrow"
"Motivation is what gets you started, Habit is what keeps you going"
"3 Months from now you will thank yourself"
These are all quotes that I found from googling "Motivational Fitness Quote Images."
The cover should contain our            VelroDyn logo.
with                                 "You are a part of the fitness revolution!"
Meal Plan
The only interior page that will change is the meal plan portion.
There are 5 different meal plans, 1200, 1500, 1750, 2000 & 2200 calories
I would also like the correct caloric number of the interior meal plan to be placed somewhere on the cover page as well, so that by looking at the cover page, the 1200 calorie meal plan book would be easily found and distinguishable from the 1500 calorie meal plan book.
Thank you!

Target Market(s)
Target market:
25-45 year old
60% female / 40% male
has at least one child
middle income
Gets coffee at brewlocke
States that they, "want to tone up"
Currently goes to the gym maybe 1-3 x per week
Industry/Entity Type
Business
Requirements
Must have
- Clear, easy to read and follow
- I have included a file labeled "Competitors Example" This is one of my old packets that I had made years ago. I do not like this style of cover with tons of pictures
- And the new packet I am wanting to have created should look much better.

Should not have
- This packet should not be plain and boring. There should not be any page that is simply white with small black text.

```html
<!DOCTYPE html>
<html lang="en">
<head>
<meta charset="utf-8">
<title>VelroDyn – Welcome Page</title>
<link href="https://fonts.googleapis.com/css2?family=Montserrat:wght@400;500;700;800&family=Black+Ops+One&display=swap" rel="stylesheet">
<style>
  :root{
    --red:#b3161b;
    --red-dark:#7e0c10;
    --ink:#2a2a2a;
    --heading-grey:#3a3a3a;
    --brand-blue:#1f6db5;
    --faint:#dcdcdc;
    --paper-top:#fbfbfb;
    --paper-bottom:#e9e9e9;
  }
  *{margin:0;padding:0;box-sizing:border-box}
  html,body{width:950px;height:1200px;overflow:hidden;background:#fff}
  .page{
    position:relative;width:950px;height:1200px;overflow:hidden;
    background:linear-gradient(180deg,var(--paper-top) 0%,#f3f3f3 55%,var(--paper-bottom) 100%);
    font-family:"Montserrat",sans-serif;color:var(--ink);
  }
  .top-band{position:absolute;left:0;top:0;width:950px;height:75px}
  .brand{position:absolute;left:62px;top:72px}
  .brand-name{font-size:46px;font-weight:700;color:var(--brand-blue);letter-spacing:-1px;line-height:1}
  .brand-tagline{font-size:11px;letter-spacing:3px;color:#555;margin-top:2px;padding-left:6px}
  .brand-faint{position:absolute;left:752px;top:60px;text-align:center}
  .brand-faint .brand-name{font-size:30px;color:var(--faint)}
  .brand-faint .brand-tagline{font-size:7px;letter-spacing:2px;color:var(--faint)}
  .slogan{
    position:absolute;left:732px;top:128px;height:740px;
    writing-mode:vertical-rl;font-family:"Black Ops One",sans-serif;
    font-size:78px;line-height:92px;color:var(--faint);white-space:nowrap;
  }
  .content{position:absolute;left:60px;top:150px;width:650px}
  .content p{font-size:15.5px;line-height:23px;text-align:justify;margin-bottom:6px}
  .intro{margin-bottom:24px}
  .section-head{border-left:4px solid #111;padding-left:12px;margin:0 0 14px 0}
  .section-head .lead{font-size:27px;font-weight:400;color:var(--heading-grey);line-height:31px}
  .section-head .title{font-size:28px;font-weight:800;color:var(--red);line-height:32px;letter-spacing:.5px}
  .block{margin-bottom:26px}
  .photo{position:absolute;left:10px;top:820px;width:927px;height:357px}
  .foot-band{position:absolute;left:10px;top:1176px;width:927px;height:24px;background:var(--red);border-top:3px solid #d8d8d8}
  .page-number{
    position:absolute;left:455px;top:1158px;width:34px;height:34px;border-radius:50%;
    background:#fff;border:2px solid #cfcfcf;font-size:14px;font-weight:500;
    display:flex;align-items:center;justify-content:center;
  }
</style>
</head>
<body>
<main class="page">
  <svg class="top-band" viewBox="0 0 950 75" aria-hidden="true">
    <polygon fill="var(--red-dark)" points="0,0 950,0 950,32 920,40 880,28 840,45 790,30 760,50 720,26 690,38 640,22 600,34 560,20 520,30 470,24 440,40 400,28 350,42 310,26 270,38 230,30 190,46 150,28 110,40 70,30 30,44 0,34"/>
    <polygon fill="var(--red)" points="0,0 950,0 950,18 900,24 860,14 800,26 740,12 680,22 620,10 560,18 500,8 440,20 380,12 320,24 260,14 200,26 140,12 80,22 20,14 0,18"/>
  </svg>

  <div class="brand">
    <div class="brand-name">VelroDyn</div>
    <div class="brand-tagline">Online Fitness Coaching</div>
  </div>
  <div class="brand-faint" aria-hidden="true">
    <div class="brand-name">VelroDyn</div>
    <div class="brand-tagline">Online Fitness Coaching</div>
  </div>

  <div class="slogan">YOU'RE NOT HERE<br>TO BE AVERAGE</div>

  <section class="content">
    <p class="intro">We are extremely excited that you have joined the VelroDyn family! Our passion is impacting people's lives and helping people achieve their health and fitness goals by combining the right fitness program with the right nutritional program, so that you ultimately achieve your fitness goal and live a healthier, fuller, happier life.</p>

    <div class="block">
      <div class="section-head">
        <div class="lead">First Things is First....</div>
        <div class="title">WHAT IS A VELRODYN?</div>
      </div>
      <p>A VelroDyn is a person who has said to themselves, “Enough is Enough!” “I am tired of the way I feel., I am tired of the way I look, and NOW is the timethat I make my health a priority and change my life by doing things correctly, which includes creating a new lifestyle and, sustainable habits and learning how to finally eat right and workout with a purpose.”</p>
    </div>

    <div class="block">
      <div class="section-head">
        <div class="lead">Second, it is imperative that</div>
        <div class="title">YOU KNOW WHAT YOUR GOAL IS?</div>
      </div>
      <p>Over the years, we have worked with literally thousands of people, and in every strategy session, we ask the new potential client, “What is your goal?” without fail, we always get the really safe answers, such as, “I want to tone up,” “I just want to be healthier,” or “I don't really have a fitness goal.”</p>
      <p>You want to tone up for a reason. You want to be healthier for a reason, and if you don't have a fitness goal at all, I'm not sure where to even start.</p>
      <p>To put it simply, people only work out for four simple reasons. You either want to look better, feel better, move better, or perform better.</p>
    </div>
  </section>

  <svg class="photo" viewBox="0 0 927 357" role="img" aria-label="Photo of a woman doing suspension-strap push-ups in a gym with a dumbbell rack behind her">
    <defs>
      <linearGradient id="photoTone" x1="0" y1="0" x2="0" y2="1">
        <stop offset="0" stop-color="#c9c9cb"/>
        <stop offset=".45" stop-color="#6b6b70"/>
        <stop offset="1" stop-color="#2b2b2f"/>
      </linearGradient>
    </defs>
    <polygon fill="url(#photoTone)" points="0,12 927,140 927,357 0,357"/>
  </svg>

  <div class="foot-band"></div>
  <div class="page-number">1</div>
</main>
</body>
</html>
```